Delivery Docket urgent plus require many other designs for more stationary after this.

We need a new delivery docket design urgently as the one we have needs updating and we have changed our company name. Please do not copy the one I have uploaded as we do not feel this looks professional enough. I uploaded it as a few designers requested to see what we are currently using thank you.
It is quite complex in that we need a range of information to be on the one docket.
We are a Transport Company based in Australia that has a wide variety of items that we deliver such as water, sand and gravels and heavy equipment transport.
We would prefer to keep this design to A5 size as we will get them made into books. We are looking for a modern professional look. Although it is only a delivery docket this is given to all our customers so needs to look impressive.

We need our new logo on the docket (WTR). There will also need to be areas for our address and contact numbers, email etc these will be supplied to the winning designer to make the final adjustments so for now just put something generic in these spaces.
Needs to have an area for customer details, purchase order number, date and docket number (docket number to be in red)
Needs a section where we can list the type of product / and or service that has been provided and the amount / qty usually 3 lines will be enough for this. Need area under this where the customer can sign name and print name to say that the goods / and or services have been received.

Also required somewhere on the docket are the words, Tax Invoice will be issued based on the information provided on this docket. Conditions on back of page

We then need a separate section on the same page which we will use internally that the staff member can tear off and hand into the office. On this section it needs to have area where the driver can list km at start of job and at end with space to calculate km travelled, details of fuel purchased eg amount and litres, vehicle that is being used. also need to log down wheel bearing temps.
prime mover needs spaces as follows
Steer axel FL____________ Steer axel FR _________ 1st drive axel L_______
1st drive axel R_________ 2nd drive axel L_______ 2nd drive axel R________

For the trailers need something similar x 2 as have 2 trailers
1st axel DS_________ 1st axel PS_________ 2nd axel DS__________
2nd axel PS_________ 3rd axel DS_________ 3rd axel PS__________

I have included a few examples of designs we have used in past and ones that we like so you can get an idea of the colours we prefer, I have included some of the designs we are currently receiving for our logo that I like so you can get idea again of colours we prefer. There is much more we need designed also such as time sheets, more delivery dockets and letter heads so there is a lot of more work available to the winning designer.

Thank you

Customers

Serif
Sans Serif

Designer to choose colors to be used in the design.

• Please don't copy old docket as we do not like it and nned new info on new design thank you

```html
<!DOCTYPE html>
<html lang="en">
<head>
<meta charset="utf-8">
<title>Delivery Docket</title>
<link href="https://fonts.googleapis.com/css2?family=Montserrat:wght@700;800&family=Raleway:ital,wght@0,400;0,500;0,700;1,500&display=swap" rel="stylesheet">
<style>
  :root{
    --ink:#111111;
    --red:#e3161b;
    --paper:#ffffff;
    --backdrop:#5c5c5c;
    --rule:#222222;
    --photo-a:#e9e9e9;
    --photo-b:#ffffff;
  }
  *{box-sizing:border-box;margin:0;padding:0}
  html,body{width:1072px;height:1200px;overflow:hidden;background:var(--backdrop)}
  body{position:relative;font-family:"Raleway",sans-serif;color:var(--ink)}
  .docket{position:absolute;left:127px;top:19px;width:930px;height:1320px;background:var(--paper);transform:scale(.88);transform-origin:0 0}
  .abs{position:absolute}

  .top-rule{left:54px;top:56px;width:823px;height:2px;background:var(--ink)}
  .title-badge{left:349px;top:34px;width:233px;height:44px;background:var(--red);border:2px solid var(--ink);border-radius:7px;box-shadow:inset 0 0 0 2px #fff;color:#fff;font:800 21px "Montserrat",sans-serif;display:flex;align-items:center;justify-content:center;letter-spacing:.2px}

  .hero-photo{left:0;top:80px;width:440px;height:170px;background:linear-gradient(90deg,var(--photo-a),var(--photo-a) 55%,var(--photo-b))}
  .brand{left:68px;top:91px;width:236px;height:135px;display:flex;align-items:center;justify-content:center;gap:14px}
  .brand-square{width:26px;height:26px;background:var(--ink)}
  .brand-name{font:700 70px "Raleway",sans-serif;color:var(--ink);letter-spacing:4px}

  .company{left:445px;top:90px;width:432px}
  .company-name{font:700 18px "Raleway",sans-serif;color:var(--red);margin-bottom:8px}
  .field{display:flex;align-items:baseline;font-size:17px;height:28px}
  .field .fill{flex:1;border-bottom:2px dotted #555;margin-left:5px;transform:translateY(-4px)}
  .field.red{color:var(--red);font-weight:700}

  .panel{border:2px solid var(--ink);border-radius:8px;overflow:hidden}
  .panel-head{height:38px;background:var(--ink);color:#fff;display:flex;align-items:center;padding:0 18px}
  .spaced{font:800 21px "Montserrat",sans-serif;letter-spacing:5px}
  .docket-no{margin-left:auto;color:var(--red);font:800 21px "Montserrat",sans-serif}

  .customer{left:55px;top:244px;width:821px;height:192px}
  .customer .rows{padding:20px 18px 0 18px}
  .customer .field{height:33px;font-size:18px}

  .dash{left:58px;width:815px;border-top:1.5px dashed #333}

  .items{left:55px;top:463px;width:821px;height:285px}
  .items table{width:100%;border-collapse:collapse;table-layout:fixed}
  .items th{height:37px;background:var(--ink);color:var(--red);font:700 20px "Raleway",sans-serif}
  .items th.qty{text-align:left;padding-left:18px;width:151px}
  .items th.amt{text-align:right;padding-right:28px;width:195px}
  .items td{height:41.5px;border-top:2px solid var(--ink)}
  .items td+td,.items th+th{border-left:2px solid var(--ink)}
  .items tr:nth-child(2) td{border-top:none}
  .note{left:0;top:756px;width:930px;text-align:center;color:var(--red);font:italic 500 16px "Raleway",sans-serif}

  .vehicle{left:55px;top:792px;width:821px;height:158px}
  .vehicle .panel-head{justify-content:center}
  .vehicle .rows{padding:20px 12px 0 12px}
  .vehicle .field{height:33px;font-size:18px}
  .vehicle .field .fill{margin-left:2px}

  .temps{left:58px;top:974px;width:815px;display:grid;grid-template-columns:113px 149px 16px 115px 149px 12px 109px 149px;row-gap:9px;align-items:center}
  .temps span{color:var(--red);font-size:15.5px;white-space:nowrap}
  .temps i{display:block;height:24px;border:1.5px solid var(--ink)}

  .signoff{top:1190px;height:97px}
  .signoff .panel-head{height:30px;justify-content:center;font:400 18px "Raleway",sans-serif}
  .received{left:46px;width:481px}
  .signed{left:542px;width:336px}
</style>
</head>
<body>
<main class="docket">
  <div class="abs top-rule"></div>
  <div class="abs title-badge">DELIVERY DOCKET</div>

  <div class="abs hero-photo" role="img" aria-label="Faded photo of a prime mover truck in a yard"></div>
  <div class="abs brand"><span class="brand-square"></span><span class="brand-name">WTR</span></div>

  <section class="abs company">
    <div class="company-name">COMPANY NAME</div>
    <div class="field">Address:<span class="fill"></span></div>
    <div class="field">Contact No:<span class="fill"></span></div>
    <div class="field">Email:<span class="fill"></span></div>
    <div class="field red">ABN:<span class="fill"></span></div>
  </section>

  <section class="abs panel customer">
    <div class="panel-head"><span class="spaced">CUSTOMER DETAILS</span><span class="docket-no">DELIVERY DOCKET NO.: 2050</span></div>
    <div class="rows">
      <div class="field">Name<span class="fill"></span></div>
      <div class="field">Address<span class="fill" style="margin-left:12px"></span></div>
      <div class="field">Purchase Order No:<span class="fill"></span><span style="margin-left:8px">Date</span><span class="fill" style="flex:0 0 188px"></span></div>
      <div class="field">Contact<span class="fill"></span></div>
    </div>
  </section>

  <div class="abs dash" style="top:449px"></div>

  <section class="abs panel items">
    <table>
      <tr><th class="qty">Quantity</th><th>Description</th><th class="amt">Amount</th></tr>
      <tr><td></td><td></td><td></td></tr>
      <tr><td></td><td></td><td></td></tr>
      <tr><td></td><td></td><td></td></tr>
      <tr><td></td><td></td><td></td></tr>
      <tr><td></td><td></td><td></td></tr>
      <tr><td></td><td></td><td></td></tr>
    </table>
  </section>
  <p class="abs note">Tax invoice will be based on information provided on this&nbsp; docket. Condition on back of page.</p>

  <div class="abs dash" style="top:783px"></div>

  <section class="abs panel vehicle">
    <div class="panel-head"><span class="spaced">VEHICLE INFORMATION</span></div>
    <div class="rows">
      <div class="field">Km at start<span class="fill"></span>Km at end<span class="fill"></span>Km travelled<span class="fill"></span></div>
      <div class="field">Details of fuel purchased (litres)<span class="fill"></span>Amount<span class="fill"></span></div>
      <div class="field">Wheel bearing temps<span class="fill"></span></div>
    </div>
  </section>

  <div class="abs dash" style="top:962px"></div>

  <section class="abs temps">
    <span>Steer axel FL</span><i></i><b></b><span>Steer axel FR</span><i></i><b></b><span>1st drive axel L</span><i></i>
    <span>1st drive axel R</span><i></i><b></b><span>2nd drive axel L</span><i></i><b></b><span>2nd drive axel R</span><i></i>
    <span>1st axel DS</span><i></i><b></b><span>1st axel PS</span><i></i><b></b><span>2nd axel DS</span><i></i>
    <span>2nd axel PS</span><i></i><b></b><span>3rd axel DS</span><i></i><b></b><span>3rd axel PS</span><i></i>
    <span>1st axel DS</span><i></i><b></b><span>1st axel PS</span><i></i><b></b><span>2nd axel DS</span><i></i>
    <span>2nd axel PS</span><i></i><b></b><span>3rd axel DS</span><i></i><b></b><span>3rd axel PS</span><i></i>
  </section>

  <section class="abs panel signoff received"><div class="panel-head">Good Received By</div></section>
  <section class="abs panel signoff signed"><div class="panel-head">Signed</div></section>
</main>
</body>
</html>
```